Business Card for beauty technology startup

Design Glimora Business Card for a Beauty, based on the website identity and colors (https://www.glimora-example.com).
Glimora is a beauty tech startup that gathers helpful product info for beauty lovers and consumers (such as availability on stores, price range and product reviews) for makeup products. The card design must be young, colorful but clean, and very modern.

Target Market(s)

woman, 15-35

Industry/Entity Type

Cosmetics

Contact Information for Business Card

Full Name, address, phone

Font styles to use
Other font styles liked:
• Advent Pro

Colors
e34297
86cfc6
ffffff
5c5c5c
e8e8e8
e667a6
b2b2b2

Requirements
Must have
• One full colored side with a creative design and another with card info
• Use Color palette: #95C5C5 and/or #D38AA5
• Use fonts: Advent Pro
• Use website identity: https://www.glimora-example.com
Nice to have
• If needed extra font: Roboto

```html
<!DOCTYPE html>
<html lang="en">
<head>
<meta charset="utf-8">
<title>Glimora Business Card</title>
<link href="https://fonts.googleapis.com/css2?family=Advent+Pro:wght@200;300;400;500;600&display=swap" rel="stylesheet">
<style>
  :root {
    --page-bg: #e6e6e6;
    --brand-pink: #cd7f9b;
    --brand-pink-deep: #bf7290;
    --ink-dark: #2f2a2c;
    --card-white: #f4f4f2;
    --teal: #86bfbf;
    --rose-text: #c9819d;
    --rule: #b9dcdc;
    --faint-mark: rgba(255, 255, 255, 0.08);
    --faint-mark-light: rgba(0, 0, 0, 0.045);
  }
  * { margin: 0; padding: 0; box-sizing: border-box; }
  html, body {
    width: 1200px;
    height: 576px;
    overflow: hidden;
    background: var(--page-bg);
    font-family: "Advent Pro", sans-serif;
  }
  .canvas {
    position: relative;
    width: 1200px;
    height: 576px;
  }
  .card {
    position: absolute;
    top: 138px;
    border-radius: 16px;
    overflow: hidden;
  }
  .card-front {
    left: 82px;
    width: 484px;
    height: 294px;
    background: linear-gradient(180deg, var(--brand-pink) 0%, var(--brand-pink-deep) 100%);
  }
  .card-back {
    left: 602px;
    width: 481px;
    height: 291px;
    background: var(--card-white);
  }
  .faint-ring {
    position: absolute;
    width: 224px;
    height: 224px;
    border-radius: 50%;
  }
  .card-front .faint-ring {
    left: 130px; top: 34px;
    border: 4px solid var(--faint-mark);
  }
  .card-back .faint-ring {
    left: 126px; top: 34px;
    border: 4px solid var(--faint-mark-light);
  }
  .brand-lockup {
    position: absolute;
    left: 105px;
    top: 120px;
    display: flex;
    align-items: center;
    gap: 38px;
  }
  .brand-dot {
    width: 53px; height: 53px;
    border: 1.6px solid var(--ink-dark);
    border-radius: 50%;
  }
  .brand-name {
    font-weight: 300;
    font-size: 44px;
    letter-spacing: 6px;
    color: var(--ink-dark);
    line-height: 1;
  }
  .contact {
    position: absolute;
    left: 0; right: 0;
    top: 90px;
    text-align: center;
  }
  .contact-name {
    font-weight: 600;
    font-size: 21px;
    letter-spacing: 0.5px;
    color: var(--teal);
    line-height: 1;
    margin-bottom: 14px;
  }
  .contact-line {
    font-weight: 500;
    font-size: 14px;
    line-height: 16.5px;
    color: var(--rose-text);
  }
  .contact-rule {
    width: 318px;
    height: 1px;
    background: var(--rule);
    margin: 5px auto 4px;
  }
</style>
</head>
<body>
  <main class="canvas">
    <section class="card card-front" aria-label="Card front">
      <div class="faint-ring"></div>
      <div class="brand-lockup">
        <span class="brand-dot"></span>
        <span class="brand-name">GLIMORA</span>
      </div>
    </section>

    <section class="card card-back" aria-label="Card back">
      <div class="faint-ring"></div>
      <div class="contact">
        <p class="contact-name">MARA ELLIS</p>
        <p class="contact-line">00 482 615 790</p>
        <p class="contact-line">hello@glimora-example.com</p>
        <p class="contact-line">www.glimora-example.com</p>
        <div class="contact-rule"></div>
        <p class="contact-line">48, Petal Avenue, Rosedale, Country - 704512</p>
      </div>
    </section>
  </main>
</body>
</html>
```